Therapy Dog Business need a brochure

I need a brochure designed for my Canine Assisted Therapy business in Victoria Australia. I have a logo already and info and photos to upload.
Best as white background and using the colours from the logo please
Updates

Hi Everyone,
I am sorry to have to revise the brief. I have added three new photos I was unable to add due to the size. I have had to wait for my photographer to change the size to add them today. I have been really inspired by all the work you have done so far. Thank you.
Could you please add the following on the brochure. (Under the individual dogs photo)
1. Pepper is the white dog. Please add the following under her picture. Pepper is one of the first Court Dogs in Australia. Working in Victoria, she has worked in the following Courts. The Halbrook Inquest Court, The Brindle Hearing Court in Collingwood, and the Fenwick Court in Melbourne CBD. Her ability to use her intuition for clients is inspiring. Please contact us for potential use in Courts. Pepper has worked at the Marlow Constabulary College, and at TALON at Mar Con. She is a stunning dog!
2. Barnaby is the golden dog. Barnaby is Peppers son, and had her instinct of intuition of who needs his help. Barnaby has an incredible soft approach as does his mother Pepper. He is incredibly safe with young children, and yet has a playful nature for adolescents and adults alike. He is soft and caring, and like his mother will go to those who need him most. Barnaby like his mother has worked at Marlow Constabulary, his time at MC included the Marlow Constabulary Directorate (MCD) Both he and his mother have very impressive CV'S!
3. Tansy the black dog. Tansy is my Therapy and Assistance dog "trainer" she is safe and stable with all the dogs and people I train for Therapy Dog Training and Assistance Dog Training. She has also been with me on my journey as a Counsellor and I have been able to work alongside her and Pepper for Counselling sessions.
She is soft, caring, and also intuitive. I am incredibly grateful for her help, as well as Pepper and Barnaby.
ALSO I am so sorry to add this but could you also add the following: Maybe in dot point?
Court Dog Availability
Therapy Dog Visits - Lawyers - Courts - Child Protection
Police Station / Ambulance Station / Fire Station - Visits
Private Therapy Dog Sessions
website and email confirmation coming soon. Thank you

Target Market(s)

First Responders

Requirements
Must have
• All the photos provided.
Should not have
• Generic photos

```html
<!DOCTYPE html>
<html lang="en">
<head>
<meta charset="utf-8">
<title>Kindred Paws – Canine Assisted Therapy Brochure</title>
<link href="https://fonts.googleapis.com/css2?family=Rubik:wght@500;600&family=Figtree:wght@400;500&family=Damion&display=swap" rel="stylesheet">
<style>
:root{
  --maroon:#6b1d22;
  --maroon-deep:#5a171c;
  --rust:#a4452c;
  --rust-band:#b0502c;
  --orange:#e9984a;
  --pink:#e27a78;
  --ink:#3a3235;
  --white:#ffffff;
  --stage:#c9c9c9;
}
*{box-sizing:border-box;margin:0;padding:0}
html,body{width:1200px;height:785px;overflow:hidden;background:var(--stage)}
body{position:relative;font-family:"Figtree",sans-serif;color:var(--ink)}
.page{position:absolute;overflow:hidden;background:var(--white)}
.page--front{left:59px;top:44px;width:532px;height:688px}
.page--back{left:623px;top:47px;width:528px;height:684px;
  background:linear-gradient(200deg,var(--rust) 0%,#8a3027 40%,var(--maroon) 80%)}
.abs{position:absolute}
.heading{font-family:"Rubik",sans-serif;font-weight:600;line-height:1.2}
.body{font-size:8px;line-height:10.4px}

/* front hero */
.hero{left:0;top:0;width:532px;height:210px}
.logo-tab{left:28px;top:0;width:97px;height:118px;background:var(--white);
  border-radius:0 0 48px 48px;display:flex;flex-direction:column;align-items:center;justify-content:center;gap:6px}
.logo-tab .dot{width:22px;height:22px;border-radius:50%;background:var(--maroon)}
.logo-name{font-family:"Rubik",sans-serif;font-weight:600;font-size:11px;color:var(--maroon);text-align:center;line-height:1.15}

.benefits-title{left:30px;top:158px;font-size:16px;color:var(--maroon)}
.benefits-title .accent{color:var(--orange)}
.blob{width:46px;height:44px;background:var(--maroon);border-radius:46% 46% 38% 38% / 58% 58% 34% 34%}
.blob--light{background:var(--white)}
.item-title{font-size:13px;color:var(--maroon);font-weight:500}
.benefit-text{left:30px;width:238px}

.join-band{left:0;top:542px;width:297px;height:27px;background:var(--pink);
  color:var(--white);font-size:16px;display:flex;align-items:center;justify-content:center}
.join-text{left:26px;top:577px;width:246px;text-align:center}
.call-btn{left:56px;top:636px;width:186px;height:19px;border-radius:10px;background:var(--maroon);
  color:var(--white);font-family:"Rubik",sans-serif;font-weight:500;font-size:11px;
  display:flex;align-items:center;justify-content:center;gap:5px}
.call-btn .ring{width:14px;height:14px;border-radius:50%;background:var(--pink);display:flex;align-items:center;justify-content:center}
.contacts{top:660px;left:21px;width:258px;display:flex;justify-content:space-between;font-size:8.6px;font-weight:500;color:var(--maroon)}
.contacts span{display:flex;align-items:center;gap:4px;white-space:nowrap}
.contacts i{display:inline-block;width:14px;height:14px;border-radius:50%;background:var(--pink)}

.what-title{left:291px;top:158px;font-size:16px;color:var(--maroon)}
.what-title .accent{color:var(--orange)}
.what-text{left:291px;top:202px;width:230px;font-size:8.9px;line-height:11.5px}
.what-text .short{display:block;width:150px}
.silhouette{left:440px;top:261px;width:92px;height:62px;
  background:linear-gradient(90deg,var(--maroon) 0%,#8b3a2c 100%);border-radius:40px 0 0 0;opacity:.9}

.why-panel{left:287px;top:321px;width:245px;height:367px;border-radius:60px 0 0 0;
  background:linear-gradient(180deg,#8a3129 0%,var(--rust) 45%,#7a2526 100%);overflow:hidden}
.why-band{left:0;top:0;width:245px;height:57px;background:linear-gradient(90deg,var(--maroon-deep),#7c2a27)}
.why-title{right:18px;top:9px;font-size:14.5px;color:var(--white);text-align:right;line-height:19px}
.why-item-title{font-size:12.5px;color:var(--white);font-weight:500}
.why-text{left:27px;width:205px;color:var(--white);font-size:8px;line-height:10.4px}

/* back page */
.back-title{left:35px;top:20px;font-family:"Damion",cursive;font-size:31px;color:var(--white)}
.back-logo{left:393px;top:23px;width:116px;height:116px;border-radius:50%;background:var(--white);
  border:3px solid var(--maroon);display:flex;align-items:center;justify-content:center}
.back-logo .logo-name{font-size:14px}
.dog-photo{left:35px;width:168px;height:119px;border:3px solid var(--white);
  box-shadow:0 6px 8px rgba(40,0,0,.35)}
.name-pill{left:222px;width:118px;height:30px;background:var(--orange);border-radius:0 16px 16px 0;
  font-family:"Damion",cursive;font-size:25px;color:var(--maroon);padding-left:14px;line-height:31px}
.dog-text{left:222px;width:296px;color:var(--white);font-size:9.3px;line-height:12.45px}
.dog-text .float-gap{float:right;width:132px;height:48px}
.back-base{left:0;top:520px;width:528px;height:164px}
.court-band{left:35px;top:583px;width:463px;height:32px;border-radius:16px;background:var(--rust-band);
  color:var(--white);font-family:"Rubik",sans-serif;font-weight:500;font-size:17px;
  display:flex;align-items:center;justify-content:center}
.avail{font-size:11.2px;color:var(--ink);display:flex;align-items:center;gap:5px;white-space:nowrap}
.tick{width:11px;height:11px;border-radius:50%;background:var(--orange);display:inline-flex;align-items:center;justify-content:center}
</style>
</head>
<body>

<section class="page page--front">
  <svg class="abs hero" viewBox="0 0 532 210" aria-hidden="true">
    <defs>
      <linearGradient id="heroFill" x1="0" y1="0" x2="1" y2="0">
        <stop offset="0" stop-color="#5a171c"/><stop offset=".6" stop-color="#6e1f24"/><stop offset="1" stop-color="#9c3f2e"/>
      </linearGradient>
    </defs>
    <path d="M0 0H532V160Q300 110 0 148Z" fill="url(#heroFill)"/>
    <path d="M0 150Q140 118 260 120" stroke="#e9984a" stroke-width="3" fill="none"/>
    <path d="M380 150Q470 160 532 190V165Q470 140 390 142Z" fill="#e27a78"/>
  </svg>
  <div class="abs" role="img" aria-label="Photo of two yellow Labradors and a black Labrador lying side by side"
       style="left:135px;top:28px;width:397px;height:122px;border-radius:70px 0 0 0;background:linear-gradient(90deg,rgba(232,205,160,.55),rgba(240,232,215,.45) 55%,rgba(30,20,22,.7))"></div>

  <div class="abs logo-tab"><span class="dot"></span><span class="logo-name">Kindred<br>Paws</span></div>

  <h2 class="abs heading benefits-title"><span class="accent">Benefits of</span><br>Canine Assisted Therapy</h2>

  <div class="abs blob" style="left:30px;top:203px"></div>
  <h3 class="abs heading item-title" style="left:91px;top:210px">Emotional Support<br>and Comfort</h3>
  <p class="abs body benefit-text" style="top:253px">Therapy dogs provide immediate emotional support, offering comfort and companionship during therapy sessions. Their calming presence helps reduce feelings of anxiety, stress, and depression, and grief, creating a safe and nurturing environment for healing.</p>

  <div class="abs blob" style="left:30px;top:312px"></div>
  <h3 class="abs heading item-title" style="left:91px;top:319px">Stress Relief and<br>Relaxation</h3>
  <p class="abs body benefit-text" style="top:362px">Interacting with dogs has been proven to reduce cortisol (stress hormone) levels and increase serotonin and oxytocin, the “feel-good” hormones. This natural relief from stress makes Canine Assisted Therapy an ideal option for individuals dealing with anxiety, trauma, PTSD, and grief,</p>

  <div class="abs blob" style="left:30px;top:425px"></div>
  <h3 class="abs heading item-title" style="left:91px;top:431px">Improved Mental<br>Health</h3>
  <p class="abs body benefit-text" style="top:474px">Therapy dogs encourage social interaction, communication, and emotional expression, helping individuals address mental health challenges such as depression, anxiety, PTSD, and grief. The unconditional love and companionship of a dog can foster trust and openness during therapy sessions.</p>

  <div class="abs join-band heading">Join the Healing Journey Today!</div>
  <p class="abs body join-text">Whether you are seeking emotional support or mental health improvement, Canine Assisted Therapy offers a unique and compassionate approach to healing. Connect with us today to learn more about how a therapy dog can help enhance your life and well-being.</p>
  <div class="abs call-btn">
    <span class="ring"><svg width="8" height="8" viewBox="0 0 24 24"><path fill="#fff" d="M6.6 10.8a15 15 0 006.6 6.6l2.2-2.2a1 1 0 011-.25 11.4 11.4 0 003.6.57 1 1 0 011 1V20a1 1 0 01-1 1A17 17 0 013 4a1 1 0 011-1h3.5a1 1 0 011 1 11.4 11.4 0 00.57 3.6 1 1 0 01-.25 1z"/></svg></span>
    Call us Today! 0400 217 639
  </div>
  <div class="abs contacts"><span><i></i>hello@kindredpaws.org</span><span><i></i>www.kindredpaws.org</span></div>

  <h2 class="abs heading what-title">What is <span class="accent">Canine<br>Assisted Therapy?</span></h2>
  <p class="abs what-text">Canine Assisted Therapy (CAT) is a unique form of therapy that integrates trained therapy dogs into the healing process. By working alongside licensed therapists, these compassionate and well-trained dogs help support individuals in overcoming emotional, physical, and psychological challenges.<span class="short">This innovative approach promotes healing, reduces stress, and enhances overall well-being.</span></p>
  <div class="abs silhouette" role="img" aria-label="Illustration of a person in a cap sitting beside a dog"></div>

  <div class="abs why-panel">
    <div class="abs why-band"></div>
    <h2 class="abs heading why-title">Why Choose<br>Canine Assisted Therapy?</h2>

    <div class="abs blob blob--light" style="left:27px;top:66px;width:42px;height:42px"></div>
    <h3 class="abs heading why-item-title" style="left:88px;top:74px">Proven<br>Effectiveness</h3>
    <p class="abs why-text" style="top:116px">Studies and testimonials highlight the positive effects therapy dogs have on emotional, psychological and physical health.</p>

    <div class="abs blob blob--light" style="left:27px;top:157px;width:42px;height:42px"></div>
    <h3 class="abs heading why-item-title" style="left:88px;top:163px">Non-Invasive<br>and Gentle</h3>
    <p class="abs why-text" style="top:205px">Therapy dogs provide a natural and non-threatening way to engage with patients, making it accessible for individuals who may feel apprehensive about traditional therapy methods.</p>

    <div class="abs blob blob--light" style="left:27px;top:259px;width:42px;height:42px"></div>
    <h3 class="abs heading why-item-title" style="left:88px;top:264px">Safe and<br>Trustworthy</h3>
    <p class="abs why-text" style="top:307px">All therapy dogs are carefully trained to work with professionals, ensuring that interactions are safe, beneficial, and appropriate for all individuals.</p>
  </div>
</section>

<section class="page page--back">
  <h1 class="abs back-title">Private Therapy Dog Sessions</h1>
  <div class="abs back-logo"><span class="logo-name">Kindred<br>Paws</span></div>

  <div class="abs dog-photo" style="top:71px;background:linear-gradient(135deg,#8fa3d6,#c9b790 60%,#e9dcc0)" role="img" aria-label="Photo of Pepper, a white Labrador, lying on a blue blanket"></div>
  <div class="abs name-pill" style="top:68px">Pepper</div>
  <p class="abs dog-text" style="top:104px"><span class="float-gap"></span>Pepper is one of the first Court Dogs in Australia. Working in Victoria, she has worked in the following Courts. The Halbrook Inquest Court, The Brindle Hearing Court in Collingwood, and the Fenwick Court in Melbourne CBD. Her ability to use her intuition for clients is inspiring. Please contact us for potential use in Courts. Pepper has worked at the Marlow Constabulary College, and at TALON at Mar Con. She is a stunning dog!</p>

  <div class="abs dog-photo" style="top:236px;background:linear-gradient(135deg,#d0603f,#e0c695 45%,#8fa3d6)" role="img" aria-label="Photo of Barnaby, a golden Labrador, lying on a blue blanket"></div>
  <div class="abs name-pill" style="top:233px">Barnaby</div>
  <p class="abs dog-text" style="top:270px">Barnaby is Peppers son, and had her instinct of intuition of who needs his help. Barnaby has an incredible soft approach as does his mother Pepper. He is incredibly safe with young children, and yet has a playful nature for adolescents and adults alike. He is soft and caring, and like his mother will go to those who need him most. Barnaby like his mother has worked at Marlow Constabulary, his time at MC included the Marlow Constabulary Directorate (MCD) Both he and his mother have very impressive CV'S!</p>

  <div class="abs dog-photo" style="top:395px;background:linear-gradient(180deg,#b8764f 0%,#8fa3d6 20%,#2a2428 60%,#8fa3d6)" role="img" aria-label="Photo of Tansy, a black Labrador, lying on a blue blanket"></div>
  <div class="abs name-pill" style="top:392px">Tansy</div>
  <p class="abs dog-text" style="top:429px">Tansy is my Therapy and Assistance dog "trainer" she is safe and stable with all the dogs and people I train for Therapy Dog Training and Assistance Dog Training. She has also been with me on my journey as a Counsellor and I have been able to work alongside her and Pepper for Counselling sessions.<br>She is soft, caring, and also intuitive. I am incredibly grateful for her help, as well as Pepper and Barnaby.</p>

  <svg class="abs back-base" viewBox="0 0 528 164" aria-hidden="true">
    <path d="M0 48Q260 0 528 36V164H0Z" fill="#fff"/>
    <path d="M0 40Q260 -8 440 24" stroke="#e9984a" stroke-width="3" fill="none"/>
    <path d="M420 30Q490 40 528 62V88Q480 50 420 34Z" fill="#e27a78"/>
  </svg>

  <div class="abs court-band">Court Dog Availability</div>
  <div class="abs avail" style="left:52px;top:618px"><span class="tick"><svg width="7" height="7" viewBox="0 0 10 10"><path d="M2 5.2l2 2 4-4.4" stroke="#fff" stroke-width="1.6" fill="none"/></svg></span>Therapy Dog Visits</div>
  <div class="abs avail" style="left:187px;top:618px"><span class="tick"><svg width="7" height="7" viewBox="0 0 10 10"><path d="M2 5.2l2 2 4-4.4" stroke="#fff" stroke-width="1.6" fill="none"/></svg></span>Lawyers</div>
  <div class="abs avail" style="left:279px;top:618px"><span class="tick"><svg width="7" height="7" viewBox="0 0 10 10"><path d="M2 5.2l2 2 4-4.4" stroke="#fff" stroke-width="1.6" fill="none"/></svg></span>Courts</div>
  <div class="abs avail" style="left:360px;top:618px"><span class="tick"><svg width="7" height="7" viewBox="0 0 10 10"><path d="M2 5.2l2 2 4-4.4" stroke="#fff" stroke-width="1.6" fill="none"/></svg></span>Child Protection</div>
  <div class="abs avail" style="left:52px;top:635px"><span class="tick"><svg width="7" height="7" viewBox="0 0 10 10"><path d="M2 5.2l2 2 4-4.4" stroke="#fff" stroke-width="1.6" fill="none"/></svg></span>Police Station</div>
  <div class="abs avail" style="left:164px;top:635px"><span class="tick"><svg width="7" height="7" viewBox="0 0 10 10"><path d="M2 5.2l2 2 4-4.4" stroke="#fff" stroke-width="1.6" fill="none"/></svg></span>Ambulance Station</div>
  <div class="abs avail" style="left:306px;top:635px"><span class="tick"><svg width="7" height="7" viewBox="0 0 10 10"><path d="M2 5.2l2 2 4-4.4" stroke="#fff" stroke-width="1.6" fill="none"/></svg></span>Fire Station</div>
  <div class="abs avail" style="left:415px;top:635px"><span class="tick"><svg width="7" height="7" viewBox="0 0 10 10"><path d="M2 5.2l2 2 4-4.4" stroke="#fff" stroke-width="1.6" fill="none"/></svg></span>Visits</div>
</section>

</body>
</html>
```